Fenwick Grading LTD - website for irrigation & Landscape Lighting & Buried service wire

Looking for a website to help promote my business with Irrigation (installation, service, etc) and buried service wire/drainage solutions.

Commercial/Residential

Landscape lighting.

I’ll get photos in the trucks and trailers to upload as well maybe the machine as well.

Target Market(s)

Homeowners who want green grass and beautiful gardens. Beautiful landscape lighting

Industry/Entity Type

Irrigation systems and landscape lighting and buried service wire to homes and offering Drainage soltions.

Coding

Coded - Design and coding required

Number of Pages Required

4 page

Colors
F0912C
F2A743
F7CA91
FBE8D2
FDF5EE

Requirements
Must have
• was hoping to link up my email on fenwickgrading@mailbox-example.net with the website if possible.
Nice to have
• Page for Irrigation, page for landscape lighting, page buried service wire & drainage soltions.

```html
<!DOCTYPE html>
<html lang="en">
<head>
<meta charset="utf-8">
<title>Fenwick Grading LTD</title>
<link href="https://fonts.googleapis.com/css2?family=Josefin+Sans:wght@400;600;700&family=Poppins:wght@400;500;600&display=swap" rel="stylesheet">
<style>
:root{
  --orange:#F0912C;
  --orange-2:#F2A743;
  --peach:#F7CA91;
  --cream:#FBE8D2;
  --ivory:#FDF5EE;
  --ink:#1d1d1d;
  --muted:#666;
  --white:#fff;
}
*{box-sizing:border-box;margin:0;padding:0}
html,body{width:1200px;height:4132px;overflow:hidden}
body{position:relative;background:var(--white);font-family:"Poppins",sans-serif;color:var(--ink)}
.abs{position:absolute}
.display{font-family:"Josefin Sans",sans-serif;text-transform:uppercase;letter-spacing:2px}
.photo{position:absolute}

/* header */
.topbar{left:0;top:0;width:1200px;height:40px;background:var(--white)}
.topbar .contact{position:absolute;top:11px;font-size:13px;color:var(--muted);display:flex;align-items:center;gap:8px}
.logo{display:flex;align-items:center;gap:12px}
.logo .mark{width:34px;height:34px;background:var(--orange);flex:none}
.logo .name{font-family:"Josefin Sans",sans-serif;font-weight:700;color:var(--orange);text-transform:uppercase;line-height:1}
.header-logo{left:40px;top:14px;z-index:3}
.header-logo .name{font-size:22px}
.nav{left:320px;top:40px;width:880px;height:48px;background:var(--orange);display:flex;align-items:center;padding-left:24px;gap:34px;z-index:3}
.nav a{color:var(--white);font-size:14px;text-decoration:none;font-weight:500}
.nav a.active{background:var(--orange-2);padding:14px 16px}
.nav .cta{margin-left:auto;margin-right:24px;background:var(--ink);padding:8px 16px;border-radius:3px}

/* hero */
.hero{left:0;top:0;width:1200px;height:850px;clip-path:polygon(0 0,100% 0,100% 88%,50% 100%,0 88%);overflow:hidden}
.hero .photo{inset:0;background:linear-gradient(180deg,#5f6b52 0%,#48533d 45%,#2f3527 100%)}
.hero-title{left:150px;top:262px;width:900px;text-align:center;color:var(--white);font-size:44px;font-weight:700;line-height:1.3;letter-spacing:3px}
.btn{display:inline-flex;align-items:center;gap:10px;background:var(--orange);color:var(--white);font-size:14px;font-weight:500;padding:12px 24px;border-radius:3px;text-decoration:none}
.hero .btn{position:absolute;left:528px;top:464px}
.slide-count{top:724px;color:var(--white);font-size:18px;font-weight:600}
.slide-line{left:492px;top:736px;width:216px;height:2px;background:rgba(255,255,255,.4)}
.slide-line i{display:block;width:50px;height:2px;background:var(--orange)}
.social-rail{left:1150px;top:300px;display:flex;flex-direction:column;align-items:center;gap:14px}
.dot{width:30px;height:30px;border-radius:50%;border:1.5px solid var(--white)}
.scroll{color:var(--white);font-size:11px;writing-mode:vertical-rl;letter-spacing:2px;margin-top:14px}
.scroll-line{width:1px;height:80px;background:var(--white)}

/* about */
.about-a{left:92px;top:928px;width:308px;height:364px;background:linear-gradient(160deg,#1f2a22,#3c3a2a 55%,#6b5a33)}
.about-b{left:400px;top:1168px;width:192px;height:164px;background:linear-gradient(180deg,#2c3f57,#6d6a58 70%,#a08a5c);border:6px solid var(--white)}
.section-title{font-family:"Josefin Sans",sans-serif;text-transform:uppercase;font-size:38px;font-weight:600;letter-spacing:3px;color:var(--ink)}
.about-title{left:632px;top:922px}
.underline{height:3px;background:var(--ink)}
.about-text{left:632px;top:984px;width:480px;font-size:13px;line-height:1.75;color:var(--muted)}
.about-text p+p{margin-top:14px}
.about-actions{left:632px;top:1276px;display:flex;align-items:center;gap:22px}
.or{font-size:14px;color:var(--muted)}
.callnow small{display:block;font-size:11px;color:var(--muted)}
.callnow b{font-size:16px;font-weight:600}

/* services */
.services{left:0;top:1480px;width:1200px;height:920px;background:linear-gradient(180deg,var(--orange-2),var(--orange));clip-path:polygon(0 13%,50% 0,100% 13%,100% 87%,50% 100%,0 87%)}
.services-title{left:0;top:1636px;width:1200px;text-align:center;color:var(--white);font-size:42px}
.services-title .underline{width:150px;margin:8px auto 0;background:var(--white)}
.card{top:1732px;width:480px;height:460px;background:var(--white)}
.card .photo{left:0;top:0;width:480px;height:364px}
.card h3{position:absolute;left:0;top:364px;width:480px;height:96px;line-height:96px;text-align:center;font-family:"Josefin Sans",sans-serif;text-transform:uppercase;font-size:28px;font-weight:600;letter-spacing:2px}

/* lighting */
.light-title{left:112px;top:2500px}
.light-title .underline{width:80px;margin-top:8px}
.light-text{left:112px;top:2566px;width:440px;font-size:13px;line-height:1.75;color:var(--muted)}
.light-btn{left:112px;top:2652px}
.light-a{left:608px;top:2492px;width:480px;height:468px;background:linear-gradient(160deg,#1d2530,#4a3a2a 55%,#8a6a3c)}
.light-b{left:112px;top:2752px;width:528px;height:268px;background:linear-gradient(180deg,#22324a,#53617a 50%,#b58650)}

/* contact */
.contact-bar{left:690px;top:3112px;width:510px;height:88px;background:var(--orange)}
.contact-title{left:160px;top:3176px;font-size:36px}
.contact-title .underline{width:80px;margin-top:6px}
.contact-text{left:160px;top:3234px;width:380px;font-size:13px;line-height:1.75;color:var(--muted)}
.info{left:160px;display:flex;align-items:center;gap:14px}
.info .ic{width:34px;height:34px;border-radius:50%;background:var(--orange);display:flex;align-items:center;justify-content:center}
.info small{display:block;font-size:11px;color:var(--muted)}
.info b{font-size:13px;font-weight:500}
.socials{left:160px;top:3514px;display:flex;gap:10px}
.socials span{width:30px;height:30px;border-radius:50%;background:var(--orange)}
.form{left:592px;top:3160px;width:456px;height:520px;background:var(--white);box-shadow:0 6px 30px rgba(0,0,0,.14);padding:36px 24px;z-index:2}
.field{height:44px;border:1px solid #ddd;font-size:12px;color:var(--muted);padding:13px 12px;margin-bottom:16px}
.field.msg{height:120px}
.form .btn{padding:11px 22px}

/* cta */
.cta-band{left:160px;top:3628px;width:980px;height:152px;background:var(--orange);display:flex;align-items:center;justify-content:center;gap:28px;color:var(--white)}
.cta-band span{font-family:"Josefin Sans",sans-serif;text-transform:uppercase;font-size:24px;letter-spacing:2px;font-weight:600}
.cta-band b{font-family:"Josefin Sans",sans-serif;font-size:48px;letter-spacing:3px;font-weight:700}

/* footer */
.footer-logo{left:0;top:3856px;width:1200px;justify-content:center}
.footer-logo .mark{width:44px;height:44px}
.footer-logo .name{font-size:34px}
.footer-nav{left:0;top:3990px;width:1200px;display:flex;justify-content:center;gap:40px}
.footer-nav a{font-size:14px;color:var(--ink);text-decoration:none}
.footer-rule{left:160px;top:4050px;width:880px;height:1px;background:#ddd}
.copy{left:0;top:4074px;width:1200px;text-align:center;font-size:12px;color:var(--muted)}
</style>
</head>
<body>

<section class="abs hero">
  <div class="photo" role="img" aria-label="Photo of a person watering a garden with a hose in the evening"></div>
  <h1 class="abs hero-title display">Irrigation Systems &amp; Landscape Lighting and Fiber Optic Installation to Homes</h1>
  <a class="btn" href="#">Get Started
    <svg width="10" height="10" viewBox="0 0 10 10"><path d="M3 1l4 4-4 4" stroke="#fff" stroke-width="1.6" fill="none"/></svg></a>
  <span class="abs slide-count" style="left:448px">01</span>
  <div class="abs slide-line"><i></i></div>
  <span class="abs slide-count" style="left:722px">05</span>
  <div class="abs social-rail">
    <span class="dot"></span><span class="dot"></span>
    <span class="scroll">Scroll Down</span>
    <span class="scroll-line"></span>
  </div>
</section>

<header>
  <div class="abs topbar">
    <span class="contact" style="left:700px">
      <svg width="12" height="12" viewBox="0 0 24 24"><path d="M6.6 10.8a15 15 0 006.6 6.6l2.2-2.2a1 1 0 011-.25 11.4 11.4 0 003.6.57 1 1 0 011 1V20a1 1 0 01-1 1A17 17 0 013 4a1 1 0 011-1h3.5a1 1 0 011 1c0 1.25.2 2.45.57 3.57a1 1 0 01-.25 1z" fill="#F0912C"/></svg>
      +1 888 888 8888</span>
    <span class="contact" style="left:870px">
      <svg width="13" height="11" viewBox="0 0 24 18"><rect x="1" y="1" width="22" height="16" rx="2" fill="#F0912C"/><path d="M1 2l11 8 11-8" stroke="#fff" stroke-width="1.8" fill="none"/></svg>
      fenwickgrading@mailbox-example.net</span>
  </div>
  <div class="abs logo header-logo"><span class="mark"></span><span class="name">Fenwick<br>Grading LTD</span></div>
  <nav class="abs nav">
    <a class="active" href="#">Home</a><a href="#">About Us</a><a href="#">Irrigation Installs</a><a href="#">Service</a><a href="#">Landscape Lighting</a><a href="#">Fiber Optic Installation</a><a class="cta" href="#">Contact Us</a>
  </nav>
</header>

<section class="about">
  <div class="photo about-a" role="img" aria-label="Photo of a house at night with lit garden lights"></div>
  <div class="photo about-b" role="img" aria-label="Photo of string lights over a patio at dusk"></div>
  <div class="abs about-title"><h2 class="section-title">About Us</h2><div class="underline" style="width:80px;margin-top:6px"></div></div>
  <div class="abs about-text">
    <p>We design, install and service irrigation systems that keep lawns green and gardens healthy through every season. Our crews also trench and bury service wire, lay drainage lines and set landscape lighting, so one team handles the work from the first marked line to the final walkthrough. Every job is planned with care, finished cleanly and backed by friendly service.</p>
    <p>From small backyards to large commercial lots, we bring the right machines and the right people to get your project done on time and on budget.</p>
  </div>
  <div class="abs about-actions">
    <a class="btn" href="#">Learn More
      <svg width="10" height="10" viewBox="0 0 10 10"><path d="M3 1l4 4-4 4" stroke="#fff" stroke-width="1.6" fill="none"/></svg></a>
    <span class="or">Or</span>
    <span class="callnow"><small>Call Us Now</small><b>+1 888 888 8888</b></span>
  </div>
</section>

<section>
  <div class="abs services"></div>
  <div class="abs services-title"><h2 class="display" style="font-weight:600">Our Services</h2><div class="underline"></div></div>
  <div class="abs card" style="left:112px">
    <div class="photo" role="img" aria-label="Photo of a commercial deck lit with string lights at night" style="background:linear-gradient(180deg,#2b2a36,#6b4a2c 60%,#a87a42)"></div>
    <h3>Commercial</h3>
  </div>
  <div class="abs card" style="left:616px">
    <div class="photo" role="img" aria-label="Photo of a sprinkler watering a green residential lawn" style="background:linear-gradient(180deg,#a9b99a,#6f9a45 50%,#4d7a2a)"></div>
    <h3>Residential</h3>
  </div>
</section>

<section>
  <div class="abs light-title"><h2 class="section-title">Landscape Lighting</h2><div class="underline"></div></div>
  <p class="abs light-text">Light up paths, patios and garden beds with warm, efficient fixtures that add safety and charm to your property long after the sun goes down.</p>
  <a class="abs btn light-btn" href="#">View More
    <svg width="10" height="10" viewBox="0 0 10 10"><path d="M3 1l4 4-4 4" stroke="#fff" stroke-width="1.6" fill="none"/></svg></a>
  <div class="photo light-a" role="img" aria-label="Photo of a lit cabin and stone garden steps at night"></div>
  <div class="photo light-b" role="img" aria-label="Photo of a waterfront patio with string lights at dusk"></div>
</section>

<section>
  <div class="abs contact-bar"></div>
  <div class="abs contact-title"><h2 class="section-title" style="font-size:36px">Contact Info</h2><div class="underline"></div></div>
  <p class="abs contact-text">Have a question or ready to start? Reach out by phone or email and our team will get back to you with a free estimate.</p>
  <div class="abs info" style="top:3372px">
    <span class="ic"><svg width="14" height="14" viewBox="0 0 24 24"><path d="M6.6 10.8a15 15 0 006.6 6.6l2.2-2.2a1 1 0 011-.25 11.4 11.4 0 003.6.57 1 1 0 011 1V20a1 1 0 01-1 1A17 17 0 013 4a1 1 0 011-1h3.5a1 1 0 011 1c0 1.25.2 2.45.57 3.57a1 1 0 01-.25 1z" fill="#fff"/></svg></span>
    <span><small>Call Us</small><b>+1 888 888 8888</b></span>
  </div>
  <div class="abs info" style="top:3440px">
    <span class="ic"><svg width="14" height="11" viewBox="0 0 24 18"><rect x="1" y="1" width="22" height="16" rx="2" fill="#fff"/><path d="M1 2l11 8 11-8" stroke="#F0912C" stroke-width="1.8" fill="none"/></svg></span>
    <span><small>Email</small><b>fenwickgrading@mailbox-example.net</b></span>
  </div>
  <div class="abs socials"><span></span><span></span></div>
  <form class="abs form">
    <div class="field">Your Name</div>
    <div class="field">Email</div>
    <div class="field">Phone Number</div>
    <div class="field msg">Enter Your Message</div>
    <a class="btn" href="#">Submit
      <svg width="10" height="10" viewBox="0 0 10 10"><path d="M3 1l4 4-4 4" stroke="#fff" stroke-width="1.6" fill="none"/></svg></a>
  </form>
</section>

<div class="abs cta-band"><span>For More Information Call Us:</span><b>+1 888 888 8888</b></div>

<footer>
  <div class="abs logo footer-logo"><span class="mark"></span><span class="name">Fenwick Grading LTD</span></div>
  <nav class="abs footer-nav">
    <a href="#">Home</a><a href="#">About Us</a><a href="#">Irrigation Installs</a><a href="#">Service</a><a href="#">Landscape Lighting</a><a href="#">Fiber Optic Installation</a><a href="#">Contact Us</a>
  </nav>
  <div class="abs footer-rule"></div>
  <p class="abs copy">©2024. All rights reserved.</p>
</footer>

</body>
</html>
```